Velmora Systems Website

Website design for our company: Velmora Systems.
The website should look fresh and IT focused. Please have a look at http://www.velmorasystems.example.au/ for our current design. We want something fresh and new, professional looking, in WordPress so we can easily make changes.

It Company

```html
<!DOCTYPE html>
<html lang="en">
<head>
<meta charset="utf-8">
<title>Velmora Systems</title>
<link href="https://fonts.googleapis.com/css2?family=Open+Sans:wght@300;400;600&display=swap" rel="stylesheet">
<style>
:root{
  --bg:#cfe3ec;
  --green:#0aa84f;
  --green-light:#22c06a;
  --blue:#0a6fc2;
  --text:#666;
  --text-soft:#888;
  --rule:#dedede;
  --footer-top:#3d3d3d;
  --footer-bottom:#282828;
  --footer-bar:#1c1c1c;
  --footer-link:#b9b9b9;
  --field:#1e1e1e;
}
*{box-sizing:border-box;margin:0;padding:0}
html,body{width:1062px;height:1200px;overflow:hidden}
body{background:var(--bg);font-family:"Open Sans",sans-serif;position:relative}
.page{position:absolute;left:88px;top:0;width:886px;height:1200px;background:#fff}

.header{position:absolute;left:0;top:0;width:886px;height:91px;
  background:linear-gradient(180deg,#0bb256 0%,var(--green) 100%)}
.brand{position:absolute;left:11px;top:26px;display:flex;align-items:center;gap:8px;
  color:#fff;font-weight:600;font-size:16px}
.brand-dot{width:34px;height:34px;border-radius:50%;background:#fff}
.call{position:absolute;right:224px;top:12px;text-align:right;color:#fff;line-height:16px}
.call-label{font-size:13px}
.call-number{font-size:15px;font-weight:600}
.call-icon{position:absolute;left:668px;top:18px}
.search{position:absolute;left:710px;top:16px;width:166px;height:28px;background:#fff;
  border-radius:2px;font-size:12px;color:#999;padding:6px 8px}
.search svg{position:absolute;right:6px;top:5px}
.search::after{content:"";position:absolute;right:28px;top:5px;width:1px;height:18px;background:#ddd}
.nav{position:absolute;left:267px;right:10px;top:62px;display:flex;justify-content:space-between;
  color:#fff;font-size:13px;font-weight:600}
.nav-active{position:absolute;left:262px;top:84px;width:51px;height:7px;background:#fff}

.hero{position:absolute;left:9px;top:104px;width:867px;height:350px;
  background:linear-gradient(100deg,#1c5b8e 0%,#17314f 30%,#111c2c 60%,#0e1724 100%)}
.hero-title{position:absolute;right:50px;top:148px;color:#fff;font-size:22px;text-align:right;line-height:28px;letter-spacing:.3px}
.hero-prev{position:absolute;left:0;top:140px;width:32px;height:70px;
  background:radial-gradient(ellipse at left,rgba(255,255,255,.7),rgba(255,255,255,0) 70%)}
.hero-next{position:absolute;right:0;top:136px;width:20px;height:80px;background:#fff;border-radius:40px 0 0 40px}
.hero-prev svg{position:absolute;left:2px;top:28px}
.hero-next svg{position:absolute;left:8px;top:33px}

.intro{position:absolute;left:20px;width:846px;top:482px;text-align:center}
.intro-lead{color:var(--blue);font-size:13px;margin-bottom:10px}
.intro-text{color:var(--text);font-size:12px;line-height:20.5px}

.rule{position:absolute;left:9px;width:869px;height:1px;background:var(--rule)}

.feature{position:absolute;top:645px;display:flex;gap:9px}
.feature-ring{width:83px;height:83px;border-radius:50%;border:2px solid var(--green-light);
  display:flex;align-items:center;justify-content:center;flex:none}
.feature-title{color:var(--green-light);font-size:22px;font-weight:300;line-height:26px;margin-top:1px}
.feature-text{color:var(--text-soft);font-size:11.5px;line-height:15.5px;margin-top:4px;width:160px}

.quote{position:absolute;left:0;width:886px;top:793px;text-align:center;color:#555;font-size:15.5px;line-height:22.4px}
.quote-mark{font-size:13px;font-weight:700;vertical-align:top;color:#444}
.quote-by{color:var(--blue);font-size:13px;margin-top:7px}

.footer{position:absolute;left:0;top:920px;width:886px;height:226px;
  background:linear-gradient(180deg,var(--footer-top),var(--footer-bottom))}
.footer h3{position:absolute;top:30px;color:#e0e0e0;font-size:13px;font-weight:400}
.footer-list{position:absolute;top:57px;list-style:none;color:var(--footer-link);font-size:11.5px;line-height:22px}
.social{position:absolute;left:20px;top:171px;display:flex;gap:4px}
.social span{width:26px;height:26px;background:#d8d8d8;border-radius:3px;display:flex;align-items:center;justify-content:center}
.field{position:absolute;left:598px;width:205px;background:var(--field);border:1px solid #3a3a3a;border-radius:3px;
  color:#777;font-size:11px;padding:8px 11px}
.submit{position:absolute;left:811px;top:170px;width:57px;height:28px;background:#5a5a5a;border-radius:3px;
  color:#e6e6e6;font-size:11.5px;text-align:center;line-height:28px}
.copyright{position:absolute;left:0;top:1146px;width:886px;height:54px;background:var(--footer-bar);
  color:#9a9a9a;font-size:11.5px;text-align:center;line-height:54px}
</style>
</head>
<body>
<div class="page">
  <header class="header">
    <div class="brand"><span class="brand-dot"></span>Velmora Systems</div>
    <div class="call"><div class="call-label">Call us</div><div class="call-number">555 014 2290</div></div>
    <svg class="call-icon" width="24" height="20" viewBox="0 0 24 20"><path d="M3 3c2-2 4-1 5 1l1 2c0 1-1 2-2 3 1 2 3 4 5 5 1-1 2-2 3-2l2 1c2 1 3 3 1 5-6 3-18-8-15-15z" fill="#fff"/><path d="M16 4a6 6 0 0 1 4 4M16 1a9 9 0 0 1 7 7" stroke="#fff" stroke-width="1.3" fill="none"/></svg>
    <div class="search">Search<svg width="16" height="16" viewBox="0 0 16 16"><circle cx="6.5" cy="6.5" r="5" stroke="#888" stroke-width="2" fill="none"/><path d="M10 10l5 5" stroke="#888" stroke-width="2.2"/></svg></div>
    <nav class="nav"><span>HOME</span><span>ABOUT US</span><span>CLIENTS</span><span>SERVICES</span><span>SUPPORTS</span><span>TESTIMONIALS</span><span>CONTACT US</span></nav>
    <div class="nav-active"></div>
  </header>

  <section class="hero" role="img" aria-label="Businessman in a suit using a tablet in front of blue-lit server racks">
    <div class="hero-prev"><svg width="12" height="14" viewBox="0 0 12 14"><path d="M9 2L3 7l6 5" stroke="#222" stroke-width="2.5" fill="none"/></svg></div>
    <div class="hero-next"><svg width="12" height="14" viewBox="0 0 12 14"><path d="M3 2l6 5-6 5" stroke="#222" stroke-width="2.5" fill="none"/></svg></div>
    <h1 class="hero-title">FOR YOUR<br>NETWORK RELATED SERVICES</h1>
  </section>

  <section class="intro">
    <p class="intro-lead">Velmora Systems is an Adelaide based company with a single objective - to excel in the support and service of all computer and IT needs.</p>
    <p class="intro-text">We provide a high level of consulting services using the most experienced engineers at a reasonable and fair price. We believe in using a Business Value approach to every aspect of computer consulting to provide our clients with the most cost effective solutions. We strongly believe that we are in business with our clients. Each thing we do must be measured against our clients' business objectives. At the end of the day our client's success is our success.</p>
  </section>

  <div class="rule" style="top:618px"></div>

  <div class="feature" style="left:24px">
    <div class="feature-ring"><svg width="26" height="26" viewBox="0 0 26 26"><g fill="var(--green-light)"><rect x="10" y="1" width="6" height="5"/><rect x="10" y="20" width="6" height="5"/><rect x="1" y="10" width="5" height="6"/><rect x="20" y="10" width="5" height="6"/><rect x="4" y="4" width="4" height="4"/><rect x="18" y="4" width="4" height="4"/><rect x="4" y="18" width="4" height="4"/><rect x="18" y="18" width="4" height="4"/></g></svg></div>
    <div><h2 class="feature-title">Network Services</h2><p class="feature-text">Aliquam ultricies, sapien vel molestie placerat, dolor ligula suscipit leo, sit amet.</p></div>
  </div>
  <div class="feature" style="left:330px">
    <div class="feature-ring"><svg width="22" height="26" viewBox="0 0 22 26"><g fill="var(--green-light)"><ellipse cx="11" cy="4" rx="10" ry="3.5"/><path d="M1 7c0 4 20 4 20 0v4c0 4-20 4-20 0z"/><path d="M1 14c0 4 20 4 20 0v4c0 4-20 4-20 0z"/></g></svg></div>
    <div><h2 class="feature-title">Servers</h2><p class="feature-text">Aliquam ultricies, sapien vel molestie placerat, dolor ligula suscipit leo, sit amet.</p></div>
  </div>
  <div class="feature" style="left:619px">
    <div class="feature-ring"><svg width="22" height="26" viewBox="0 0 22 26"><path d="M11 1L1 5v7c0 7 5 11 10 13 5-2 10-6 10-13V5z" fill="var(--green-light)"/></svg></div>
    <div><h2 class="feature-title">Security</h2><p class="feature-text">Aliquam ultricies, sapien vel molestie placerat, dolor ligula suscipit leo, sit amet.</p></div>
  </div>

  <div class="rule" style="top:758px"></div>

  <blockquote class="quote">
    <p><span class="quote-mark">&#10077;</span>&nbsp; I have always found the team extremely helpful with their advice over the phone.<br>They also have the ability to access our computers remotely, and can rectify most problems quite swiftly.<br>I have no hesitation in recommending Velmora Systems for all of your IT needs. &nbsp;<span class="quote-mark">&#10078;</span></p>
    <p class="quote-by">- &nbsp;Daniel Harrow B.Pharm, Greenfield Chemists, Northvale</p>
  </blockquote>

  <footer class="footer">
    <h3 style="left:19px">Navigation Menu</h3>
    <ul class="footer-list" style="left:19px"><li>Home</li><li>About us</li><li>Clients</li><li>Services</li></ul>
    <ul class="footer-list" style="left:112px"><li>Support</li><li>Testimonials</li><li>Contact us</li></ul>
    <h3 style="left:260px">Our Services</h3>
    <ul class="footer-list" style="left:260px"><li>On-site Service</li><li>Remote Desktop Support</li><li>Medical IT Service</li><li>Pharmacy IT Service</li></ul>
    <ul class="footer-list" style="left:418px"><li>Website Design</li><li>Disaster Recovery</li><li>Hardware/ Software supply</li><li>Consumables</li></ul>
    <div class="social">
      <span aria-label="Social link"></span>
      <span aria-label="Social link"></span>
      <span aria-label="Social link"></span>
      <span aria-label="Email"><svg width="14" height="10" viewBox="0 0 14 10"><rect width="14" height="10" rx="1" fill="#555"/><path d="M0 1l7 5 7-5" stroke="#d8d8d8" stroke-width="1.3" fill="none"/></svg></span>
      <span aria-label="Feed"><svg width="13" height="13" viewBox="0 0 13 13"><circle cx="2" cy="11" r="2" fill="#555"/><path d="M0 6a7 7 0 0 1 7 7M0 1a12 12 0 0 1 12 12" stroke="#555" stroke-width="2" fill="none"/></svg></span>
    </div>
    <h3 style="left:602px">Contact us</h3>
    <div class="field" style="top:66px;height:32px">Name</div>
    <div class="field" style="top:102px;height:32px">E-mail</div>
    <div class="field" style="top:139px;height:60px">Comment</div>
    <div class="submit">SUBMIT</div>
  </footer>
  <div class="copyright">Copyright &nbsp;© 2014 &nbsp;Velmora Systems . &nbsp;All rights reserved.</div>
</div>
</body>
</html>
```